Need help in designing new business card utilizing our new logo.

BuildMark Solutions works with Construction Business Owners, Managers & IT Professionals to strengthen software usage and increase user productivity.

Our Construction Accounting and Mobile Field Management Software Clients engage with us in the following areas:

New Software Implementations
Software Re-Implementations
Redesigning Software Usage at the User Level
Project Coordination & Management
Continued Software Support

Old tag line:
Weighing Options - Implementing Solutions

www.buildmark-solutions.example

Ridge 4 is a product, but not needed for a new business card.

```html
<!DOCTYPE html>
<html lang="en">
<head>
<meta charset="utf-8">
<title>BuildMark Solutions – Business Card</title>
<link href="https://fonts.googleapis.com/css2?family=Roboto:wght@400;500;700&display=swap" rel="stylesheet">
<style>
  :root{
    --backdrop:#3a3a3b;
    --card:#2b2c2e;
    --brand-blue:#1d4f9c;
    --band-blue:#1f4d95;
    --silver:#c9cacc;
    --wave-dark:#1d1e20;
    --white:#ffffff;
  }
  *{margin:0;padding:0;box-sizing:border-box}
  html,body{width:799px;height:1200px;overflow:hidden}
  body{background:var(--backdrop);font-family:"Roboto",Arial,sans-serif;color:var(--white);position:relative}
  .card{position:absolute;left:80px;width:640px;height:366px;background:var(--card);border-radius:22px;overflow:hidden;box-shadow:0 14px 30px rgba(0,0,0,.45)}
  .card--front{top:140px}
  .card--back{top:700px}

  .brand{display:flex;align-items:center;gap:14px}
  .brand__mark{width:30px;height:30px;background:var(--silver);flex:none}
  .brand__name{font-weight:500;font-size:30px;letter-spacing:2px;color:var(--silver);line-height:1.05}
  .card--front .brand{position:absolute;top:48px;left:0;right:0;justify-content:center}

  .services{position:absolute;top:132px;left:0;right:0;height:118px;background:var(--band-blue);display:flex;flex-direction:column;justify-content:center;align-items:center;gap:3px;font-size:17px;line-height:1.25;text-align:center}
  .web-line{position:absolute;top:286px;left:0;right:0;display:flex;justify-content:center;align-items:center;gap:22px;font-size:16px}
  .web-line__rule{width:48px;height:2px;background:var(--white)}

  .waves{position:absolute;inset:0;width:640px;height:366px}
  .holder{position:absolute;top:26px;left:34px}
  .holder__name{color:var(--brand-blue);font-weight:700;font-size:22px}
  .holder__role{font-size:12px;margin-top:2px}
  .contacts{position:absolute;top:94px;left:34px;list-style:none;font-size:14px;line-height:19px}
  .contacts li{display:flex;align-items:center;gap:10px}
  .contacts svg{width:11px;height:11px;flex:none}
  .card--back .brand{position:absolute;top:80px;right:34px}
  .card--back .brand__name{color:var(--brand-blue);font-size:26px}
  .card--back .brand__mark{background:var(--brand-blue);width:28px;height:28px}
  .address{position:absolute;top:156px;right:34px;text-align:right;font-size:15px;line-height:20px;font-style:normal}
  .tagline{position:absolute;bottom:22px;right:40px;text-align:right;font-size:16px;line-height:21px}
</style>
</head>
<body>

<section class="card card--front" aria-label="Card front">
  <div class="brand">
    <span class="brand__mark"></span>
    <span class="brand__name">BUILDMARK SOLUTIONS</span>
  </div>
  <div class="services">
    <p>New Software Implementations &nbsp;|&nbsp; Software Re-Implementations</p>
    <p>Redesigning Software Usage at the User Level</p>
    <p>Project Coordination &amp; Management &nbsp;|&nbsp; Continued Software Support</p>
  </div>
  <div class="web-line">
    <span class="web-line__rule"></span>
    <span>www.buildmark-solutions.example</span>
    <span class="web-line__rule"></span>
  </div>
</section>

<section class="card card--back" aria-label="Card back">
  <svg class="waves" viewBox="0 0 640 366" aria-hidden="true">
    <circle cx="-20" cy="40" r="34" fill="var(--brand-blue)"/>
    <path d="M0,222 C110,320 290,300 420,290 C520,280 590,290 640,300 L640,366 L0,366 Z" fill="var(--brand-blue)"/>
    <path d="M0,206 C110,304 290,284 420,274 C520,264 590,274 640,284" fill="none" stroke="var(--wave-dark)" stroke-width="14"/>
    <path d="M0,190 C110,288 290,268 420,258 C520,248 590,258 640,268" fill="none" stroke="var(--silver)" stroke-width="10"/>
  </svg>

  <div class="holder">
    <p class="holder__name">Dana R. Whitfield</p>
    <p class="holder__role">Owner</p>
  </div>

  <ul class="contacts">
    <li><svg viewBox="0 0 12 12"><rect x="3" y="0" width="6" height="12" rx="1.5" fill="var(--brand-blue)"/></svg>555-201-4832</li>
    <li><svg viewBox="0 0 12 12"><path d="M2,1 L5,1 L6,4 L4,5 C5,7 6,8 8,9 L9,7 L12,8 L12,11 C6,12 0,6 2,1 Z" fill="var(--brand-blue)"/></svg>800-555-0150 ext. 100</li>
    <li><svg viewBox="0 0 12 12"><rect x="0" y="2" width="12" height="8" fill="var(--brand-blue)"/><path d="M0,2 L6,7 L12,2" fill="none" stroke="var(--card)" stroke-width="1"/></svg>dana.whitfield@buildmark-solutions.example</li>
    <li><svg viewBox="0 0 12 12"><circle cx="6" cy="6" r="5.5" fill="var(--brand-blue)"/><path d="M0.5,6 H11.5 M6,0.5 V11.5" stroke="var(--card)" stroke-width="1"/></svg>www.buildmark-solutions.example</li>
  </ul>

  <div class="brand">
    <span class="brand__mark"></span>
    <span class="brand__name">BUILDMARK SOLUTIONS</span>
  </div>

  <address class="address">
    14B Market Street - PMB 118<br>
    Lakeview Falls, NY 10001
  </address>

  <p class="tagline">Weighing Options<br>Implementing Solutions</p>
</section>

</body>
</html>
```